A Must Standout Business Card Design

I need A card that stands out from the rest. Possibly raised letters or Metallic card, Shiny or glossy, Looking for a more modern look or something throwback design would be nice. So i'm a open to different designs. I have a logo but not to happy with it. I will send it on a sample business card I do like.I might like you to tweak the designed card I am sending you. A new logo may be in order too. Make logo something that can be engraved on metal. I was thinking possibly QJ in a box or QJ mirror image or Backward E then a forward B in a circle. The name of my company is QJ Forge Inc. I designed an innovative hand tool to remove Valve Cores. I call the tool the Stem Pin Clasper. My tool grips and holds onto valve cores like no other tool does. Check it out at my website stempinclasp.example Maybe put a picture of the tool on the card raised or embossed or that spot gloss.
Updates
Everybody I must say have sent over some awesome designs! Every submission has been my favorite so I will be making my decision after the deadline. Nice work everyone!
Target Market(s)
Automotive people, People who wholesale refrigeration parts and equipment, People who use tools
Industry/Entity Type
Business
Contact Information for Business Card
QJ Forge Inc., 2817 Hollowmere Ave. Unit K Danford IL 61739, Marcus Tolliver President, 555-281-9467, Stempinclasp.example, Logo
Look and feel
Each slider illustrates characteristics of the customer's brand and the style your logo design should communicate.

```html
<!DOCTYPE html>
<html lang="en">
<head>
<meta charset="utf-8">
<title>QJ Forge Inc. – Business Card</title>
<link rel="stylesheet" href="https://fonts.googleapis.com/css2?family=Bebas+Neue&display=swap">
<style>
  :root {
    --page: #ffffff;
    --metal-light: #e4e4e4;
    --metal-mid: #c4c4c4;
    --metal-dark: #9c9c9c;
    --brand: #f4f4f4;
    --title-grey: #b8b8b8;
    --title-shadow: #5a5a5a;
    --ink: #111111;
    --icon-fg: #ffffff;
    --tool-light: #d8d8d8;
    --tool-dark: #8e8e8e;
  }
  * { margin: 0; padding: 0; box-sizing: border-box; }
  html, body {
    width: 702px;
    height: 1200px;
    overflow: hidden;
    background: var(--page);
  }
  .card {
    position: relative;
    width: 702px;
    height: 1200px;
    border-radius: 30px;
    overflow: hidden;
    font-family: "Bebas Neue", "Arial Narrow", sans-serif;
    background:
      repeating-linear-gradient(90deg,
        rgba(255,255,255,0.18) 0px, rgba(255,255,255,0) 2px,
        rgba(0,0,0,0.06) 3px, rgba(255,255,255,0) 5px,
        rgba(255,255,255,0.1) 7px, rgba(0,0,0,0.04) 9px),
      linear-gradient(100deg, var(--metal-dark) 0%, var(--metal-light) 28%, var(--metal-mid) 50%, var(--metal-light) 72%, var(--metal-dark) 100%);
  }
  .brand-name {
    position: absolute;
    top: 150px;
    left: 0;
    width: 100%;
    text-align: center;
    font-size: 96px;
    line-height: 1;
    letter-spacing: 4px;
    color: var(--brand);
  }
  .product-visual {
    position: absolute;
    left: 190px;
    top: 315px;
    width: 240px;
    height: 615px;
    border-radius: 60px 60px 20px 20px;
    background: linear-gradient(90deg, var(--tool-dark), var(--tool-light) 45%, var(--tool-dark));
    opacity: 0.55;
  }
  .person {
    position: absolute;
    top: 488px;
    left: 0;
    width: 100%;
    text-align: center;
    color: var(--title-grey);
    text-shadow: -2px -2px 0 rgba(255,255,255,0.6), 3px 3px 3px var(--title-shadow);
    line-height: 1.08;
  }
  .person-name { font-size: 72px; letter-spacing: 2px; }
  .person-role { font-size: 72px; letter-spacing: 3px; }
  .contact-list {
    position: absolute;
    left: 58px;
    top: 978px;
    list-style: none;
  }
  .contact-item {
    display: flex;
    align-items: center;
    height: 55px;
    color: var(--ink);
    font-size: 31px;
    letter-spacing: 0.5px;
  }
  .contact-item.spaced { letter-spacing: 3px; font-size: 35px; }
  .contact-icon {
    flex: 0 0 auto;
    width: 48px;
    height: 48px;
    margin-right: 6px;
  }
</style>
</head>
<body>
  <div class="card">
    <div class="product-visual" role="img" aria-label="Photo of the Stem Pin Clasper valve core tool on a key ring"></div>

    <div class="brand-name">QJ Forge Inc.</div>

    <div class="person">
      <div class="person-name">Marcus Tolliver</div>
      <div class="person-role">President</div>
    </div>

    <ul class="contact-list">
      <li class="contact-item">
        <svg class="contact-icon" viewBox="0 0 48 48" aria-hidden="true">
          <circle cx="24" cy="24" r="24" fill="var(--ink)"/>
          <path d="M24 11 L38 24 H34 V36 H27 V28 H21 V36 H14 V24 H10 Z" fill="var(--icon-fg)"/>
        </svg>
        2817 Hollowmere Ave. Unit K Danford IL 61739
      </li>
      <li class="contact-item spaced">
        <svg class="contact-icon" viewBox="0 0 48 48" aria-hidden="true">
          <circle cx="24" cy="24" r="24" fill="var(--ink)"/>
          <path d="M15 12 L20 12 L22 19 L19 22 Q22 28 27 30 L30 27 L37 29 L37 34 Q35 37 31 37 Q14 33 11 17 Q11 13 15 12 Z" fill="var(--icon-fg)"/>
        </svg>
        555-281-9467
      </li>
      <li class="contact-item spaced">
        <svg class="contact-icon" viewBox="0 0 48 48" aria-hidden="true">
          <circle cx="24" cy="24" r="24" fill="var(--ink)"/>
          <circle cx="27" cy="20" r="8" fill="none" stroke="var(--icon-fg)" stroke-width="4"/>
          <line x1="21" y1="26" x2="12" y2="35" stroke="var(--icon-fg)" stroke-width="5" stroke-linecap="round"/>
        </svg>
        www.stempinclasp.example
      </li>
    </ul>
  </div>
</body>
</html>
```